Packaging Design For Slatetab Accessories

Brightmoor Gadget Works (brightmoorgadgetworks.example) sells computer accessories to USA retailers. We are developing a line of Slatetab accessories and would like to dramatically improve our current design. The design should feel more upmarket. Use of soft colors, simple graphics and clean fonts (similar to Varnow, Holdex and Marlowe) is something to consider in your design.

Since many of our items are in standard size box we don't require designers to create special box (package) die-line; please use the die-line from the attached Car Charger + Cable artwork and design a theme within our die-line. You can create new icons and graphics, you only need to keep the image of the cable and charger in place (according to die-line)

Artwork of the Screen Protector and Retractable Sync Cable are attached as a **reference only** to the types of items we will be selling. The design theme will be used for most of our products.

The design should resonate with the Pearwood consumer.

The budget for this project has been increased.

Designers only need to create art for the Car Charger + Cable.   The die-line is provided, so you only need to design within our die-line.

(all other die-lies are attached for your **reference** as to other items we sell)

Best,
Ned

Reason: The deadline has been extended to provide designers additional time to submit revisions. For those who have not yet submitted initial designs please do so soon. Thank you. Ned

Reason: The deadline has been extended to allow designers appropriate time to make revisions. Because the deadline occurs at 3:49am Australian EST I also want to give extra time over the weekend for those in US/Canada/Europe. Thank you for all for your submissions. Best, Ned

Please submit revisions or initial designs soon.    The deadline will not be extended further as we need to make decision soon.

Thanks to all designers who participated.

Best,
Ned

Product will be sold at retail stores in USA.

Target consumer is users of Pearwood Slatetab, Tunebud, Callslate and other tablet/mobile devices.

Computer

• Use dieline of the Car Charger + Cable provided. Create new design within the dieline we provided.

Add new icons, new graphics, color as you desire.

Include the copy from the attached artwork.

Use "Made for Slatetab,Callslate,Tunebud" logo provided (attached)
• Please do not use simple "all white" design.

```html
<!DOCTYPE html>
<html lang="en">
<head>
<meta charset="utf-8">
<title>USB Car Charger – Box Dieline Artwork</title>
<link rel="stylesheet" href="https://fonts.googleapis.com/css2?family=Quicksand:wght@400;500;600&display=swap">
<style>
  :root {
    --paper: #ffffff;
    --navy: #031c26;
    --rust: #b83208;
    --rust-text: #b5330e;
    --ink: #0e1a22;
    --cut-line: #e0201e;
    --measure: #111111;
    --glue-zone: #cfe0f5;
    --photo-dark: #1d2226;
    --photo-mid: #4a5156;
    --photo-light: #eef0f2;
  }
  html, body {
    margin: 0;
    padding: 0;
    width: 1171px;
    height: 1200px;
    overflow: hidden;
    background: var(--paper);
  }
  .dieline-sheet {
    display: block;
    width: 1171px;
    height: 1200px;
    font-family: "Quicksand", sans-serif;
  }
  .cut { fill: none; stroke: var(--cut-line); stroke-width: 1; vector-effect: non-scaling-stroke; }
  .measure-line { fill: none; stroke: var(--measure); stroke-width: 0.8; vector-effect: non-scaling-stroke; }
  .measure-head { fill: var(--paper); stroke: var(--measure); stroke-width: 0.8; vector-effect: non-scaling-stroke; }
  .measure-label { font-family: Arial, sans-serif; font-size: 13px; fill: var(--measure); }
  .glue-zone { fill: var(--glue-zone); }
  .panel-navy { fill: var(--navy); }
  .panel-rust { fill: var(--rust); }
  .title-dark { fill: var(--ink); font-weight: 500; }
  .title-accent { fill: var(--rust-text); font-weight: 500; }
  .subtitle { fill: var(--ink); font-size: 17px; font-weight: 500; }
  .side-title { fill: var(--paper); font-size: 40px; font-weight: 500; }
  .side-subtitle { fill: var(--paper); font-size: 20px; font-weight: 500; }
  .block-heading { fill: var(--paper); font-size: 12.5px; font-weight: 500; }
  .block-body { fill: var(--paper); font-size: 7px; font-weight: 500; }
  .device-label { fill: var(--paper); font-size: 9.5px; font-weight: 500; }
  .device-icon { fill: none; stroke: var(--paper); stroke-width: 0.9; }
  .brand-name { fill: var(--navy); font-size: 8px; font-weight: 600; }
  .brand-mark { fill: var(--navy); }
</style>
</head>
<body>
<svg class="dieline-sheet" viewBox="0 0 880 902" xmlns="http://www.w3.org/2000/svg" aria-label="USB Car Charger box dieline with artwork">
  <defs>
    <linearGradient id="car-interior" x1="0" y1="0" x2="1" y2="1">
      <stop offset="0" stop-color="var(--photo-mid)"/>
      <stop offset="0.55" stop-color="var(--photo-dark)"/>
      <stop offset="1" stop-color="#2c3237"/>
    </linearGradient>
    <linearGradient id="cable-shot" x1="0" y1="0" x2="0" y2="1">
      <stop offset="0" stop-color="#ffffff"/>
      <stop offset="1" stop-color="var(--photo-light)"/>
    </linearGradient>
  </defs>

  <!-- glue zone behind right bottom flap -->
  <rect class="glue-zone" x="680" y="705" width="115" height="130"/>

  <!-- side panel -->
  <rect class="panel-navy" x="200" y="200" width="118" height="455"/>
  <g transform="translate(258 590) rotate(-90)">
    <text class="side-title" x="0" y="0">USB Car Charger</text>
    <text class="side-subtitle" x="0" y="26">+charging and sync cable</text>
  </g>

  <!-- front panel title -->
  <text x="338" y="275" font-size="37"><tspan class="title-dark">USB </tspan><tspan class="title-accent">Car Charger</tspan></text>
  <text class="subtitle" x="650" y="299" text-anchor="end">+charging and sync cable</text>

  <!-- product imagery -->
  <rect x="318" y="337" width="219" height="100" fill="url(#car-interior)" role="img" aria-label="Photo of the car charger plugged into a car dashboard socket"/>
  <rect x="537" y="337" width="143" height="100" fill="url(#cable-shot)" role="img" aria-label="Photo of the charging and sync cable with dock and USB connectors"/>

  <!-- copy block -->
  <rect class="panel-rust" x="318" y="437" width="219" height="218"/>
  <text class="block-heading" x="336" y="467">Smart but Powerful</text>
  <text class="block-body" x="336" y="481">Charge your Slatetab, Callslate or Tunebud at the fastest</text>
  <text class="block-body" x="336" y="491">possible speed. Get unlimited play and standby</text>
  <text class="block-body" x="336" y="501">time with the low-profile car charger.</text>
  <text class="block-heading" x="336" y="541">Features:</text>
  <text class="block-body" x="336" y="555">Charge your Slatetab, Callslate or Tunebud at the fastest</text>
  <text class="block-body" x="336" y="565">possible speed. Get unlimited play and standby</text>
  <text class="block-body" x="336" y="575">time with the low-profile car charger.</text>

  <!-- made-for block -->
  <rect class="panel-navy" x="537" y="437" width="143" height="218"/>
  <text class="block-heading" x="579" y="466">Made for</text>
  <g class="device-icon">
    <rect x="581" y="482" width="10" height="14" rx="1.5"/>
    <circle cx="586" cy="492" r="2.4"/>
    <rect x="583" y="484" width="6" height="4"/>
    <rect x="582" y="513" width="8" height="16" rx="1.8"/>
    <line x1="584.5" y1="526.5" x2="587.5" y2="526.5"/>
    <rect x="580" y="544" width="12" height="16" rx="1.5"/>
  </g>
  <text class="device-label" x="598" y="494">Tunebud</text>
  <text class="device-label" x="598" y="525">Callslate</text>
  <text class="device-label" x="598" y="556">Slatetab</text>

  <!-- brand -->
  <rect class="brand-mark" x="454" y="684" width="8" height="8"/>
  <text class="brand-name" x="466" y="691.5">Brightmoor Gadget Works</text>

  <!-- cut lines -->
  <g class="cut">
    <path d="M318 200 V70 Q318 55 333 55 H665 Q680 55 680 70 V200"/>
    <line x1="318" y1="76" x2="680" y2="76"/>
    <path d="M210 200 V145 Q210 138 217 138 H306 Q318 138 318 150"/>
    <path d="M680 200 V150 Q680 138 692 138 H788 Q795 138 795 145 V200"/>
    <path d="M200 200 L166 222 V632 L200 655"/>
    <line x1="200" y1="200" x2="318" y2="200"/>
    <line x1="680" y1="200" x2="795" y2="200"/>
    <path d="M318 655 Q322 720 380 720 H680"/>
    <path d="M795 200 V720"/>
    <path d="M200 655 V718 H208 V890 H318 V655"/>
    <line x1="200" y1="655" x2="318" y2="655"/>
    <path d="M680 720 V780 H795 V720"/>
  </g>

  <!-- dimensions -->
  <g class="measure-line">
    <line x1="40" y1="122" x2="216" y2="122"/>
    <line x1="40" y1="200" x2="100" y2="200"/>
    <line x1="40" y1="720" x2="100" y2="720"/>
    <line x1="63" y1="122" x2="63" y2="720"/>
    <line x1="318" y1="790" x2="318" y2="805"/>
    <line x1="318" y1="796" x2="678" y2="796"/>
    <line x1="678" y1="790" x2="678" y2="855"/>
    <line x1="678" y1="840" x2="795" y2="840"/>
    <line x1="795" y1="833" x2="795" y2="848"/>
  </g>
  <g class="measure-head">
    <path d="M63 122 L58 137 H68 Z"/>
    <path d="M63 200 L58 185 H68 Z"/>
    <path d="M63 200 L58 215 H68 Z"/>
    <path d="M63 720 L58 705 H68 Z"/>
    <path d="M318 796 L333 791 V801 Z"/>
    <path d="M678 796 L663 791 V801 Z"/>
    <path d="M678 840 L693 835 V845 Z"/>
    <path d="M795 840 L780 835 V845 Z"/>
  </g>
  <text class="measure-label" x="28" y="165">1"</text>
  <text class="measure-label" x="24" y="427">6.5"</text>
  <text class="measure-label" x="486" y="792">4.5"</text>
  <text class="measure-label" x="727" y="858">1.5"</text>
</svg>
</body>
</html>
```